BUSINESS CARD DESIGN

NAME- DALE VORSKIN
PHONE NUMER - 555- 714-9082
EMAIL- OFFICE@TRV-GROUNDMAKRZ.COM
BACK OF CARD- SPEACIALIZES IN LAND CLEARING, FORESTRY MUCLHING AND EXCAVATION

Contact Information for Business Card

NAME- DALE VORSKIN PHONE NUMER - 555- 714-9082 EMAIL- OFFICE@TRV-GROUNDMAKRZ.COM BACK OF CARD- SPEACIALIZES IN LAND CLEARING , MUCLHING AND EXCAVATION

```html
<!DOCTYPE html>
<html lang="en">
<head>
<meta charset="utf-8">
<title>Traverse Groundmakrz – Business Card</title>
<link rel="stylesheet" href="https://fonts.googleapis.com/css2?family=Montserrat:wght@400;500;600;700&display=swap">
<style>
  :root {
    --backdrop: #d8d2c8;
    --card: #0b0b0b;
    --card-edge: #151515;
    --gold: #f6b417;
    --white: #f2f2f2;
    --muted: #bdbdbd;
    --faint: #202020;
    --faint-ring: #1a1a1a;
  }
  * { margin: 0; padding: 0; box-sizing: border-box; }
  html, body {
    width: 900px; height: 1200px; overflow: hidden;
    background: var(--backdrop);
    font-family: "Montserrat", sans-serif;
  }
  .canvas { position: relative; width: 900px; height: 1200px; }

  .card {
    position: absolute;
    background: linear-gradient(135deg, var(--card-edge) 0%, var(--card) 45%);
    border-radius: 24px;
    box-shadow: 0 8px 18px rgba(0,0,0,0.35);
    overflow: hidden;
  }
  .card--front { left: 80px; top: 130px; width: 742px; height: 442px; }
  .card--back  { left: 78px; top: 638px; width: 744px; height: 440px; }

  /* brand lockup */
  .brand { position: absolute; display: flex; flex-direction: column; align-items: center; }
  .brand__ring { border-radius: 50%; border: 4px solid currentColor; }
  .brand__name {
    font-weight: 600; text-align: center; letter-spacing: 0.08em; line-height: 1.25;
  }
  .brand__phone { font-weight: 600; letter-spacing: 0.3em; margin-top: 10px; }

  .brand--front { left: 45px; top: 22px; width: 260px; color: var(--gold); }
  .brand--front .brand__ring { width: 120px; height: 120px; }
  .brand--front .brand__name { font-size: 20px; margin-top: 16px; }
  .brand--front .brand__phone { font-size: 12px; }

  .brand--back { left: 0; right: 0; top: 50px; color: var(--white); }
  .brand--back .brand__ring { width: 160px; height: 160px; }
  .brand--back .brand__name { font-size: 30px; margin-top: 24px; }
  .brand--back .brand__phone { font-size: 17px; margin-top: 16px; }
  .brand__specialties {
    margin-top: 22px; font-size: 13px; font-weight: 500;
    letter-spacing: 0.14em; color: var(--gold); text-align: center;
  }

  .brand--faint { left: 410px; top: 180px; width: 300px; color: var(--faint); }
  .brand--faint .brand__ring { width: 170px; height: 170px; border-color: var(--faint-ring); border-width: 6px; }
  .brand--faint .brand__name { font-size: 22px; margin-top: 10px; }

  /* person */
  .person { position: absolute; right: 50px; top: 46px; text-align: right; }
  .person__name { color: var(--gold); font-weight: 700; font-size: 25px; letter-spacing: 0.01em; }
  .person__title { color: var(--white); font-weight: 400; font-size: 16px; margin-top: 4px; }

  /* contact list */
  .contact { position: absolute; left: 38px; top: 325px; list-style: none; }
  .contact__item {
    display: flex; align-items: center; gap: 10px;
    color: var(--white); font-size: 16px; font-weight: 400; height: 28px;
  }
  .contact__icon { width: 14px; height: 14px; flex: none; fill: var(--gold); }
</style>
</head>
<body>
<main class="canvas">

  <section class="card card--front" aria-label="Card front">
    <div class="brand brand--faint" aria-hidden="true">
      <div class="brand__ring"></div>
      <div class="brand__name">TRAVERSE GROUNDMAKRZ</div>
    </div>

    <div class="brand brand--front">
      <div class="brand__ring"></div>
      <div class="brand__name">TRAVERSE<br>GROUNDMAKRZ LLC</div>
      <div class="brand__phone">555-714-9082</div>
    </div>

    <div class="person">
      <div class="person__name">DALE VORSKIN</div>
      <div class="person__title">Managing Director</div>
    </div>

    <ul class="contact">
      <li class="contact__item">
        <svg class="contact__icon" viewBox="0 0 24 24"><path d="M6.6 10.8a15.1 15.1 0 0 0 6.6 6.6l2.2-2.2a1 1 0 0 1 1-.25 11.4 11.4 0 0 0 3.6.57 1 1 0 0 1 1 1V20a1 1 0 0 1-1 1A17 17 0 0 1 3 4a1 1 0 0 1 1-1h3.5a1 1 0 0 1 1 1c0 1.25.2 2.45.57 3.57a1 1 0 0 1-.25 1z"/></svg>
        <span>555- 714-9082</span>
      </li>
      <li class="contact__item">
        <svg class="contact__icon" viewBox="0 0 24 24"><path d="M2 5h20v14H2z"/><path d="M3 6l9 7 9-7" fill="none" stroke="#0b0b0b" stroke-width="1.8"/></svg>
        <span>OFFICE@TRV-GROUNDMAKRZ.COM</span>
      </li>
      <li class="contact__item">
        <svg class="contact__icon" viewBox="0 0 24 24"><circle cx="12" cy="12" r="10"/><path d="M2 12h20M12 2c3 3 3 17 0 20M12 2c-3 3-3 17 0 20" fill="none" stroke="#0b0b0b" stroke-width="1.6"/></svg>
        <span>WWW.TRV-GROUNDMAKRZ.COM</span>
      </li>
    </ul>
  </section>

  <section class="card card--back" aria-label="Card back">
    <div class="brand brand--back">
      <div class="brand__ring"></div>
      <div class="brand__name">TRAVERSE GROUNDMAKRZ LLC</div>
      <div class="brand__phone">555-714-9082</div>
      <div class="brand__specialties">SPECIALIZES IN LAND CLEARING, FORESTRY MULCHING &amp; EXCAVATION</div>
    </div>
  </section>

</main>
</body>
</html>
```